New business card/stationary for a consulting company

I am looking for a clean and very professional looking business card for my consulting company as well as corresponding stationary. I am uploading our logo. I like simple and powerful for the feel. No graphics but I am open on everything else. Below is my contact information but would like the final to be in a version I can add my employees information into and print. Thank you.

Daniel Whitcombe
dan@ferncliffadvisory.com
2870 North 9th Avenue, Summit Floor, Elm Ridge, Illinois 60531
www.ferncliffadvisory.com

Industry/Entity Type

Consulting

Contact Information for Business Card

Daniel Whitcombe
dan@ferncliffadvisory.com
www.ferncliffadvisory.com

Font styles to use
Serif
Sans Serif

Requirements
Must have
• Our logo and the business card details.
Nice to have
• our website www.ferncliffadvisory.com

```html
<!DOCTYPE html>
<html lang="en">
<head>
<meta charset="utf-8">
<title>Ferncliff Advisory — Business Card</title>
<link rel="stylesheet" href="https://fonts.googleapis.com/css2?family=Questrial&family=Source+Sans+3:wght@400;600&display=swap">
<style>
  :root {
    --navy: #0d0f6e;
    --white: #ffffff;
    --ink: #3a3a3a;
    --backdrop: #ecebe8;
    --edge: rgba(0,0,0,0.12);
  }
  * { box-sizing: border-box; margin: 0; padding: 0; }
  html, body { width: 1200px; height: 900px; overflow: hidden; }
  body {
    background: var(--backdrop);
    position: relative;
    font-family: "Source Sans 3", "Helvetica Neue", Arial, sans-serif;
  }
  .card {
    position: absolute;
    width: 560px;
    height: 320px;
    box-shadow: 0 6px 18px var(--edge);
  }
  .card-front {
    left: 150px;
    top: 130px;
    background: var(--navy);
    display: flex;
    flex-direction: column;
    align-items: center;
    justify-content: center;
    gap: 18px;
  }
  .front-mark {
    width: 44px;
    height: 44px;
    background: var(--white);
  }
  .front-name {
    font-family: "Questrial", "Century Gothic", sans-serif;
    color: var(--white);
    font-size: 30px;
    letter-spacing: 0.06em;
    text-transform: uppercase;
  }
  .card-back {
    left: 490px;
    top: 450px;
    background: var(--white);
    padding: 48px 44px;
  }
  .back-company {
    font-family: "Questrial", "Century Gothic", sans-serif;
    color: var(--navy);
    font-size: 33px;
    letter-spacing: 0.05em;
    text-transform: uppercase;
    white-space: nowrap;
  }
  .back-mark {
    position: absolute;
    right: 44px;
    top: 140px;
    width: 120px;
    height: 120px;
    background: var(--navy);
  }
  .person-name {
    margin-top: 34px;
    font-family: "Source Sans 3", Arial, sans-serif;
    font-weight: 600;
    color: var(--navy);
    font-size: 19px;
    letter-spacing: 0.06em;
    text-transform: uppercase;
  }
  .address {
    margin-top: 12px;
    font-style: normal;
    color: var(--ink);
    font-size: 15px;
    line-height: 1.35;
  }
  .contact-list {
    list-style: none;
    margin-top: 14px;
    color: var(--ink);
    font-size: 15px;
    line-height: 1.45;
  }
  .contact-list li { display: flex; align-items: center; gap: 8px; }
  .contact-icon { width: 13px; height: 13px; fill: var(--navy); flex: none; }
</style>
</head>
<body>
  <section class="card card-front" aria-label="Card front">
    <div class="front-mark"></div>
    <div class="front-name">Ferncliff Advisory</div>
  </section>

  <section class="card card-back" aria-label="Card back">
    <div class="back-company">Ferncliff Advisory</div>
    <div class="back-mark"></div>
    <div class="person-name">Daniel Whitcombe</div>
    <address class="address">
      2870 North 9th Avenue,<br>
      Summit Floor, Elm Ridge,<br>
      Illinois 60531
    </address>
    <ul class="contact-list">
      <li>
        <svg class="contact-icon" viewBox="0 0 16 16" aria-hidden="true"><path d="M1 3h14v10H1z M1 3l7 6 7-6" fill="var(--navy)"/><path d="M1.5 3.5l6.5 5.5 6.5-5.5" fill="none" stroke="#fff" stroke-width="1.2"/></svg>
        dan@ferncliffadvisory.com
      </li>
      <li>
        <svg class="contact-icon" viewBox="0 0 16 16" aria-hidden="true"><circle cx="8" cy="8" r="7"/><path d="M1 8h14M8 1c-3 3.5-3 10.5 0 14M8 1c3 3.5 3 10.5 0 14" fill="none" stroke="#fff" stroke-width="1"/></svg>
        www.ferncliffadvisory.com
      </li>
    </ul>
  </section>
</body>
</html>
```